Birch And Harbor Website A Website design for book editing

A website design for book editing

Our proofreading, editing and manuscript review packages are specifically tailored to help you publish the best possible version of your story.

NEED HELP PUBLISHING A BESTSELLER?

If you’re looking for professional book editing services from senior publishing industry insiders, look no further. Besides editing, we can also answer all your publishing questions and get you started building your author platform.

OUR SERVICES

We've carefully structured our packages to maximize value for every budget.

PRICING

$.02
PER WORD
Proofreading
Line Edit (Copy-editing)
Fix spelling and grammar
Sales copy/summary revision

$.04
PER WORD
Proofreading
Line Edit (Copy-editing)
Fix spelling and grammar
Organization and content
Plot and pacing
Manuscript Review

$.06
PER WORD
Proofreading
Line Edit (Copy-editing)
Fix spelling and grammar
Organization and content
Plot and pacing
Manuscript Review
Formatting (print and ebook)
Pre-publication proofread

OUR PROCESS

Send us a sample of your book. Our caffeine-fueled, eagle-eyed editors will go through it and then email you with their comments and suggestions. You can ask them any questions you want. They will look for…

Typos and grammatical errors.
Spelling and word choice issues
Punctuation and style
Word choice, clarity and flow.
Sentence structure and craft
If your writing is already clean, then they’ll discuss bigger picture things with you, like theme, concept, purpose, audience, potential market and branding (including title, subtitle, and tagline or elevator pitch).

Once you feel comfortable and confident in an editor’s expertise, skill and knowledge, and are ready to move ahead, we’ll send an invoice for the first half of the total word count so the editor can get started. We’ll charge the rest when the project is close to completion.

Target Market(s)

Authors

Industry/Entity Type

Book Publisher

Coding

Coded - Design and coding required

Number of Pages Required

1 page

Requirements
Must have
• OUR SERVICES
• We've carefully structured our packages to maximize value for every budget.
• PRICING
• $.02
• PER WORD
• Proofreading
• Line Edit (Copy-editing)
• Fix spelling and grammar
• Sales copy/summary revision
• $.04
• PER WORD
• Proofreading
• Organization and content
• Plot and pacing
• Manuscript Review
• $.06
• PER WORD
• Proofreading
• Plot and pacing
• Manuscript Review
• Formatting (print and ebook)
• Pre-publication proofread

```html
<!DOCTYPE html>
<html lang="en">
<head>
<meta charset="utf-8">
<title>Birch And Harbor — Book Editing</title>
<link href="https://fonts.googleapis.com/css2?family=Montserrat:wght@400;500;600;700;800&display=swap" rel="stylesheet">
<style>
:root{
  --red:#e0242b;
  --red-soft:#ef5a5f;
  --ink:#1f1f1f;
  --dark:#262626;
  --charcoal:#333333;
  --text:#3a3a3a;
  --muted:#666;
  --grey-bg:#eeeeee;
  --white:#ffffff;
}
*{box-sizing:border-box;margin:0;padding:0}
html,body{width:1200px;height:3913px;overflow:hidden}
body{font-family:"Montserrat",Arial,sans-serif;color:var(--text);background:var(--white);position:relative}
.abs{position:absolute}
svg{display:block}

/* top bar */
.topbar{left:0;top:0;width:1200px;height:37px;background:var(--white)}
.topbar .social{left:96px;top:11px;display:flex;gap:18px}
.topbar .social span{width:14px;height:14px;border-radius:50%;background:var(--ink)}
.topbar .contact-band{right:0;top:0;width:704px;height:37px;background:var(--red);clip-path:polygon(30px 0,100% 0,100% 100%,0 100%)}
.contact-band .item{top:9px;color:var(--white);font-size:15px;display:flex;align-items:center;gap:10px;font-weight:500;white-space:nowrap}

/* header */
.header{left:0;top:37px;width:1200px;height:130px;background:var(--white);box-shadow:0 2px 6px rgba(0,0,0,.06)}
.brand{left:91px;top:38px;display:flex;align-items:center;gap:10px;font-weight:700;font-size:36px;color:var(--red);letter-spacing:-.5px;white-space:nowrap}
.brand i{width:16px;height:16px;background:var(--red);display:block}
.nav{top:64px;display:flex;font-size:13px;font-weight:600;color:var(--ink)}
.nav a{position:absolute;white-space:nowrap;text-decoration:none;color:var(--ink)}
.nav a.active{color:var(--red)}
.nav a.active::after{content:"";position:absolute;left:0;right:0;top:27px;height:3px;background:var(--red)}

/* hero */
.hero{left:0;top:167px;width:1200px;height:527px;background:linear-gradient(100deg,#3a3d40 0%,#6b6e70 40%,#9a9c9d 70%,#7b7d7e 100%)}
.hero .shade{inset:0;background:linear-gradient(90deg,rgba(0,0,0,.45),rgba(0,0,0,.05))}
.hero h1{left:149px;top:145px;font-size:37px;line-height:52px;font-weight:700;color:var(--white);letter-spacing:.5px}
.hero p{left:149px;top:253px;width:440px;font-size:16px;line-height:30px;color:var(--white);font-weight:500}
.btn{display:flex;align-items:center;justify-content:center;border-radius:30px;font-weight:700;font-size:15px;letter-spacing:.3px;white-space:nowrap}
.btn-red{background:var(--red);color:var(--white)}
.hero .btn{left:149px;top:321px;width:169px;height:44px}
.hero .arrow{top:228px;width:38px;height:38px;border:2px solid rgba(255,255,255,.85);border-radius:50%}

/* section titles */
.title{width:1200px;left:0;text-align:center;color:var(--red);font-size:33px;font-weight:700;letter-spacing:.5px}
.lead{width:1200px;left:0;text-align:center;color:var(--ink);font-size:15px}

/* why choose us */
.why-photo{left:159px;top:918px;width:334px;height:303px;background:linear-gradient(135deg,#d9d6d4,#b7b2ae 60%,#e0dcda)}
.why-badge{left:245px;top:1140px;width:285px;height:112px;background:rgba(236,85,90,.9);color:var(--white);padding:26px 22px}
.why-badge h4{font-size:20px;font-weight:600}
.why-badge p{font-size:13px;margin-top:10px}
.feature{left:556px;width:490px;height:100px}
.feature .icon{left:0;top:0;width:68px;height:68px;display:flex;align-items:center;justify-content:center}
.feature .icon.red{background:var(--red)}
.feature .icon.dark{background:var(--ink)}
.feature h3{left:83px;top:-2px;font-size:17px;font-weight:700;color:var(--ink);white-space:nowrap}
.feature p{left:83px;top:28px;width:400px;font-size:13px;line-height:26px;color:var(--text)}

/* pricing */
.pricing{left:0;top:1341px;width:1200px;height:981px;background:var(--grey-bg)}
.card{background:var(--white);box-shadow:0 4px 14px rgba(0,0,0,.12)}
.card .head{left:0;top:0;width:100%;background:var(--ink);color:var(--white);text-align:center}
.card .price{width:100%;text-align:center;font-size:46px;font-weight:700;color:var(--white)}
.card .per{width:100%;text-align:center;font-size:18px;font-weight:700;color:var(--white)}
.card .pill{left:50%;transform:translateX(-50%);width:196px;height:50px;border-radius:26px;background:var(--white);box-shadow:0 3px 8px rgba(0,0,0,.18);display:flex;align-items:center;justify-content:center;font-size:16px;font-weight:700;color:var(--ink)}
.card ul{list-style:none;width:100%;text-align:center;font-size:17px;color:var(--ink);line-height:40px}
.card .foot{left:0;bottom:0;width:100%;background:var(--charcoal)}
.card .foot .btn{left:50%;transform:translateX(-50%);width:150px;height:40px;background:var(--white);color:var(--ink);font-size:14px}
.card.standard .head,.card.standard .foot{background:var(--red)}

/* process */
.process-intro{left:150px;top:2446px;width:900px;text-align:center;font-size:14px;line-height:29px;color:var(--ink)}
.check{left:128px;width:365px;height:66px;display:flex;align-items:center;gap:22px;padding-left:26px;font-size:16px;color:var(--ink);white-space:nowrap}
.check.on{background:var(--white);box-shadow:0 2px 10px rgba(0,0,0,.18);left:128px}
.check svg{flex:none}
.process-copy{left:564px;top:2585px;width:520px;font-size:13.5px;line-height:29px;color:var(--ink)}
.process-copy p+p{margin-top:10px}

/* testimonials */
.testimonials{left:0;top:3026px;width:1200px;height:640px;background:var(--grey-bg)}
.avatar{left:548px;top:157px;width:110px;height:110px;border-radius:50%;background:linear-gradient(160deg,#c9b6a3,#8b7564);border:4px solid var(--white);box-shadow:0 2px 8px rgba(0,0,0,.2)}
.quote{font-size:90px;font-weight:800;color:var(--ink);line-height:1;font-family:Georgia,"Times New Roman",serif}
.dots{left:566px;top:457px;display:flex;gap:13px}
.dots span{width:16px;height:16px;border-radius:50%;background:#9a9a9a}
.dots span.on{background:var(--ink)}

/* footer */
.footer{left:0;top:3500px;width:1200px;height:413px}
.footer .logo-box{left:91px;top:148px;width:308px;height:125px;background:var(--white);display:flex;align-items:center;justify-content:center;gap:10px;font-size:27px;font-weight:700;color:var(--red);white-space:nowrap}
.footer .logo-box i{width:14px;height:14px;background:var(--red);display:block;flex:none}
.footer h5{font-size:20px;font-weight:700;color:var(--white);letter-spacing:.5px;white-space:nowrap}
.footer ul{list-style:none;font-size:14px;font-weight:600;color:var(--white);line-height:23px}
.footer .touch{font-size:14px;font-weight:500;color:var(--white);display:flex;align-items:center;gap:14px;white-space:nowrap}
.footer .rule{left:0;top:341px;width:1200px;height:1px;background:#4a4a4a}
.footer .copy{left:91px;top:367px;font-size:13px;color:#e5e5e5}
.footer .social{left:920px;top:368px;display:flex;gap:22px}
.footer .social span{width:13px;height:13px;border-radius:50%;background:#dcdcdc}
</style>
</head>
<body>

<!-- top bar -->
<div class="abs topbar">
  <div class="abs social"><span></span><span></span><span></span><span></span><span></span><span></span></div>
  <div class="abs contact-band">
    <div class="abs item" style="left:160px">
      <svg width="18" height="14" viewBox="0 0 18 14"><rect x="0.5" y="0.5" width="17" height="13" fill="#fff"/><path d="M1 1l8 7 8-7" fill="none" stroke="#e0242b" stroke-width="1.6"/></svg>
      contact@birchandharbor.com
    </div>
    <div class="abs item" style="left:470px">
      <svg width="16" height="16" viewBox="0 0 24 24"><circle cx="12" cy="12" r="11" fill="none" stroke="#fff" stroke-width="2"/><path d="M8 6c1 0 1.5 2.5 1 3l-1 1c.8 2 2.2 3.4 4 4l1-1c.5-.5 3 0 3 1s-1 3-3 2c-4-1.5-6.5-4-7.5-8C5 6.5 7 6 8 6z" fill="#fff"/></svg>
      +1 555 014 2870
    </div>
  </div>
</div>

<!-- header -->
<header class="abs header">
  <div class="abs brand"><i></i>Birch And Harbor</div>
  <nav class="abs nav" style="left:0">
    <a class="active" style="left:488px">HOME</a>
    <a style="left:564px">ABOUT US</a>
    <a style="left:668px">OUR SERVICES</a>
    <a style="left:800px">PRICING</a>
    <a style="left:892px">OUR PROCESS</a>
    <a style="left:1020px">CONTACT US</a>
  </nav>
</header>

<!-- hero -->
<section class="abs hero" role="img" aria-label="Photo of a man in an office chair reading and marking up a manuscript">
  <div class="abs shade"></div>
  <h1 class="abs">NEED HELP PUBLISHING<br>A BESTSELLER</h1>
  <p class="abs">Sed ut perspiciatis unde omnis iste natus error sit voluptatem accusantium</p>
  <div class="abs btn btn-red">READ MORE</div>
  <div class="abs arrow" style="left:49px"><svg width="34" height="34" viewBox="0 0 34 34"><path d="M20 10l-7 7 7 7" fill="none" stroke="#fff" stroke-width="2"/></svg></div>
  <div class="abs arrow" style="left:1111px"><svg width="34" height="34" viewBox="0 0 34 34"><path d="M14 10l7 7-7 7" fill="none" stroke="#fff" stroke-width="2"/></svg></div>
</section>

<!-- why choose us -->
<h2 class="abs title" style="top:784px">WHY CHOOSE US</h2>
<p class="abs lead" style="top:845px">We've carefully structured our packages to maximize value for every budget.</p>
<div class="abs why-photo" role="img" aria-label="Photo of a hand writing on a printed page with a red pen"></div>
<div class="abs why-badge"><h4>New Book Publish</h4><p>Get new books for half of the price</p></div>

<div class="abs feature" style="top:908px">
  <div class="abs icon red"><svg width="26" height="26" viewBox="0 0 24 24"><path d="M12 2l3 6.5 7 .8-5.2 4.8 1.4 7L12 17.6 5.8 21l1.4-7L2 9.3l7-.8z" fill="#fff"/></svg></div>
  <h3 class="abs">100% CLIENT'S SATISFACTION</h3>
  <p class="abs">But I must explain to you how all this mistaken idea of denouncing pleasure and praising pain was born and I will give you a complete account of the system.</p>
</div>
<div class="abs feature" style="top:1031px">
  <div class="abs icon dark"><svg width="26" height="26" viewBox="0 0 24 24"><rect x="2" y="10" width="5" height="11" fill="#fff"/><path d="M9 21V10l4-7c1.5 0 2.5 1 2 3l-1 3h6c1.2 0 2 1 1.7 2.2l-2 8c-.3 1-1 1.8-2 1.8z" fill="#fff"/></svg></div>
  <h3 class="abs">USER FRIENDLY DESIGN QUALITY</h3>
  <p class="abs">But I must explain to you how all this mistaken idea of denouncing pleasure and praising pain was born and I will give you a complete account of the system.</p>
</div>
<div class="abs feature" style="top:1156px">
  <div class="abs icon dark"><svg width="30" height="26" viewBox="0 0 30 24"><circle cx="15" cy="7" r="4" fill="#fff"/><path d="M8 20c0-4 3-7 7-7s7 3 7 7z" fill="#fff"/><circle cx="6" cy="9" r="3" fill="#fff"/><circle cx="24" cy="9" r="3" fill="#fff"/><path d="M1 19c0-3 2-5 5-5 1 0 2 .3 2.6.8L7 19zM29 19c0-3-2-5-5-5-1 0-2 .3-2.6.8L23 19z" fill="#fff"/></svg></div>
  <h3 class="abs">GREAT IMPRESSION ON WEBSITE VISITOR</h3>
  <p class="abs">But I must explain to you how all this mistaken idea of denouncing pleasure and praising pain was born and I will give you a complete account of the system.</p>
</div>

<!-- pricing -->
<section class="abs pricing">
  <h2 class="abs title" style="top:83px">OUR PRICING LIST</h2>
  <p class="abs lead" style="top:140px;font-size:14px">Sed ut perspiciatis unde omnis iste natus error sit voluptatem accusantium</p>

  <div class="abs card" style="left:60px;top:219px;width:331px;height:658px">
    <div class="abs head" style="height:139px">
      <div class="abs price" style="top:20px">$.02</div>
      <div class="abs per" style="top:83px">PER WORD</div>
    </div>
    <div class="abs pill" style="top:114px">Normal</div>
    <ul class="abs" style="top:184px"><li>Proofreading</li><li>Line Edit (Copy-editing)</li><li>Fix spelling and grammar</li><li>Sales copy/summary revision</li></ul>
    <div class="abs foot" style="height:92px"><div class="abs btn" style="top:26px">BUY NOW</div></div>
  </div>

  <div class="abs card standard" style="left:430px;top:196px;width:340px;height:707px">
    <div class="abs head" style="height:139px">
      <div class="abs price" style="top:20px">$.04</div>
      <div class="abs per" style="top:83px">PER WORD</div>
    </div>
    <div class="abs pill" style="top:114px">STANDARD</div>
    <ul class="abs" style="top:182px"><li>Proofreading</li><li>Line Edit (Copy-editing)</li><li>Fix spelling and grammar</li><li>Sales copy/summary revision</li><li>Organization and content</li><li>Plot and pacing</li><li>Manuscript Review</li></ul>
    <div class="abs foot" style="height:94px"><div class="abs btn" style="top:27px">BUY NOW</div></div>
  </div>

  <div class="abs card" style="left:804px;top:219px;width:336px;height:658px">
    <div class="abs head" style="height:139px">
      <div class="abs price" style="top:20px">$.06</div>
      <div class="abs per" style="top:83px">PER WORD</div>
    </div>
    <div class="abs pill" style="top:114px">HUGE</div>
    <ul class="abs" style="top:184px"><li>Proofreading</li><li>Line Edit (Copy-editing)</li><li>Fix spelling and grammar</li><li>Sales copy/summary revision</li><li>Organization and content</li><li>Plot and pacing</li><li>Manuscript Review</li><li>Formatting (print and ebook)</li><li>Pre-publication proofread</li></ul>
    <div class="abs foot" style="height:92px"><div class="abs btn" style="top:26px">BUY NOW</div></div>
  </div>
</section>

<!-- process -->
<h2 class="abs title" style="top:2378px">OUR PROCESS</h2>
<p class="abs process-intro">Send us a sample of your book. Our caffeine-fueled, eagle-eyed editors will go through it and then email you<br>with their comments and suggestions. You can ask them any questions you want.<br>They will look for…</p>

<div class="abs check on" style="top:2584px">
  <svg width="20" height="20" viewBox="0 0 20 20"><path d="M3 2l14 7-6 1.5L8 17z" fill="#e0242b"/></svg>Typos and grammatical errors
</div>
<div class="abs check" style="top:2654px">
  <svg width="22" height="18" viewBox="0 0 22 18"><rect x="1" y="3" width="20" height="14" fill="none" stroke="#555" stroke-width="1.6"/><path d="M4 8h14M4 12h10" stroke="#555" stroke-width="1.6"/></svg>Spelling and word choice issues
</div>
<div class="abs check" style="top:2710px">
  <svg width="18" height="20" viewBox="0 0 18 20"><rect x="2" y="1" width="14" height="18" fill="none" stroke="#555" stroke-width="1.6"/><path d="M6 6h6M6 10h6M6 14h3" stroke="#555" stroke-width="1.6"/></svg>Punctuation and style
</div>
<div class="abs check" style="top:2766px">
  <svg width="18" height="20" viewBox="0 0 18 20"><rect x="2" y="1" width="14" height="18" fill="none" stroke="#555" stroke-width="1.6"/><path d="M5 7l2 2 5-5M6 14h6" fill="none" stroke="#555" stroke-width="1.6"/></svg>Word choice, clarity and flow
</div>
<div class="abs check" style="top:2822px">
  <svg width="20" height="20" viewBox="0 0 20 20"><path d="M3 17L15 5l2 2L5 19H3z" fill="none" stroke="#555" stroke-width="1.6"/><path d="M2 12l6-6M2 8l3-3" stroke="#555" stroke-width="1.6"/></svg>Sentence structure and craft
</div>

<div class="abs process-copy">
  <p>If your writing is already clean, then they'll discuss bigger picture things with you, like theme,concept, purpose, audience, potential market and branding (including title, subtitle, and tagline or elevator pitch).</p>
  <p>Once you feel comfortable and confident in an editor's expertise, skill and knowledge, and are ready to move ahead, we'll send an invoice for the first half of the total word count so the editor can get started. We'll charge the rest when the project is close to completion.</p>
</div>
<div class="abs btn btn-red" style="left:564px;top:2830px;width:193px;height:58px;font-size:16px">READ MORE</div>

<!-- testimonials -->
<section class="abs testimonials">
  <h2 class="abs title" style="top:68px">TESTIMONIALS</h2>
  <div class="abs quote" style="left:306px;top:170px">&ldquo;</div>
  <div class="abs avatar" role="img" aria-label="Portrait photo of the client giving the testimonial"></div>
  <div class="abs" style="left:0;top:308px;width:1200px;text-align:center;font-size:21px;font-weight:700;color:var(--ink)">Maya Ellison</div>
  <p class="abs" style="left:190px;top:364px;width:820px;text-align:center;font-size:14px;line-height:29px;color:var(--ink)">But I must explain to you how all this mistaken idea of denouncing pleasure and praising pain was born and I will give you a complete account of the system</p>
  <div class="abs dots"><span></span><span class="on"></span><span></span></div>
  <div class="abs quote" style="left:930px;top:440px">&rdquo;</div>
</section>

<!-- footer -->
<footer class="abs footer">
  <svg class="abs" style="left:0;top:0" width="1200" height="413" viewBox="0 0 1200 413">
    <path d="M0 55 C 60 5, 120 0, 200 20 L 1200 130 L 1200 413 L 0 413 Z" fill="#262626"/>
  </svg>
  <div class="abs logo-box"><i></i>Birch And Harbor</div>
  <h5 class="abs" style="left:569px;top:126px">QUICK LNKS</h5>
  <ul class="abs" style="left:573px;top:166px"><li>HOME</li><li>ABOUT US</li><li>OUR SERVICES</li><li>PRICING</li><li>OUR PROCESS</li><li>CONTACT US</li></ul>
  <h5 class="abs" style="left:866px;top:126px">GET IN TOUCH</h5>
  <div class="abs touch" style="left:866px;top:170px">
    <svg width="20" height="15" viewBox="0 0 18 14"><rect x="0.5" y="0.5" width="17" height="13" fill="#fff"/><path d="M1 1l8 7 8-7" fill="none" stroke="#262626" stroke-width="1.6"/></svg>
    contact@birchandharbor.com
  </div>
  <div class="abs touch" style="left:866px;top:208px">
    <svg width="20" height="20" viewBox="0 0 24 24"><circle cx="12" cy="12" r="11" fill="none" stroke="#fff" stroke-width="2"/><path d="M8 6c1 0 1.5 2.5 1 3l-1 1c.8 2 2.2 3.4 4 4l1-1c.5-.5 3 0 3 1s-1 3-3 2c-4-1.5-6.5-4-7.5-8C5 6.5 7 6 8 6z" fill="#fff"/></svg>
    +1 555 014 2870
  </div>
  <div class="abs rule"></div>
  <div class="abs copy">© 2018 Birch And Harbor. All Rights Reserved</div>
  <div class="abs social"><span></span><span style="background:var(--red)"></span><span></span><span></span><span></span><span></span></div>
</footer>

</body>
</html>
```